Rack Card Design Project

We are a locally family owned public golf course. We would like to have a rack card designed that can be used for multiple applications. The colors in our logo are grey, blue, and white. Please use those in the card design. The company logo, contact information, address, and summer pricing should be included. I've included some pictures that may or may not be used. I'm also open to suggestions....use one photo, multiple photos, a stock photo or image representing golf etc.

```html
<!DOCTYPE html>
<html lang="en">
<head>
<meta charset="utf-8">
<title>Pinewood Bay Golf Club – Summer Rates Rack Card</title>
<link rel="stylesheet" href="https://fonts.googleapis.com/css2?family=Montserrat:wght@400;500;800&family=Roboto:wght@400;500;700&family=Roboto+Condensed:wght@700&display=swap">
<style>
  :root {
    --navy: #133560;
    --grey-light: #d3d3d3;
    --grey-band: #7c7c7c;
    --ink: #2a2a2a;
    --white: #ffffff;
    --page: #ffffff;
  }
  * { box-sizing: border-box; margin: 0; padding: 0; }
  html, body { width: 1200px; height: 1200px; overflow: hidden; background: var(--page); }
  .rack-card {
    position: absolute; left: 345px; top: 45px;
    width: 510px; height: 1110px;
    background: var(--white);
    font-family: "Roboto", sans-serif;
    overflow: hidden;
  }
  .hero-photo {
    position: absolute; left: 0; top: 0; width: 510px; height: 290px;
    background: linear-gradient(180deg, #b9b7b0 0%, #9c9a88 28%, #4f5a3a 52%, #3f5a2e 72%, #4e6b34 100%);
  }
  .club-seal {
    position: absolute; left: 167px; top: 199px; width: 176px; height: 176px;
    border-radius: 50%; background: var(--white);
    border: 6px solid var(--grey-light);
    display: flex; align-items: center; justify-content: center; text-align: center;
  }
  .club-seal span {
    font-family: "Montserrat", sans-serif; font-weight: 800; font-size: 19px;
    line-height: 1.15; color: var(--navy);
  }
  .title {
    position: absolute; left: 0; width: 100%; top: 380px; text-align: center;
    font-family: "Montserrat", sans-serif; font-weight: 800; font-size: 47px;
    color: var(--navy); letter-spacing: -0.5px;
  }
  .season {
    position: absolute; left: 0; width: 100%; top: 436px; text-align: center;
    font-family: "Montserrat", sans-serif; font-weight: 400; font-size: 31px;
    color: #3a3a3a; letter-spacing: 0.5px;
  }
  .rate-heading {
    position: absolute; left: 139px; top: 498px; width: 232px; height: 44px;
    background: var(--navy); color: var(--white);
    font-family: "Roboto Condensed", sans-serif; font-weight: 700; font-size: 25px;
    display: flex; align-items: center; justify-content: center;
  }
  .rate-table { position: absolute; left: 99px; width: 313px; border-collapse: collapse; }
  .rate-table.primary { top: 553px; }
  .rate-table.secondary { top: 693px; }
  .rate-table td { height: 40px; padding: 0; text-align: center; }
  .rate-table .slot { width: 156px; font-size: 17px; letter-spacing: 0.3px; }
  .rate-table .price { width: 157px; font-size: 26px; }
  .is-light { background: var(--grey-light); color: var(--ink); }
  .is-dark { background: var(--navy); color: var(--white); }
  .kids-offer {
    position: absolute; left: 98px; top: 782px; width: 314px; height: 98px;
    background: var(--navy); color: var(--white); text-align: center;
    font-family: "Montserrat", sans-serif; font-weight: 500; font-size: 23px;
    line-height: 30px; letter-spacing: 0.4px;
    display: flex; flex-direction: column; justify-content: center;
  }
  .kids-offer strong { font-weight: 800; }
  .lunch {
    position: absolute; left: 0; width: 100%; top: 892px; text-align: center;
    font-size: 30px; color: #1e1e1e;
  }
  .lunch-hours {
    position: absolute; left: 0; width: 100%; top: 929px; text-align: center;
    font-family: "Roboto Condensed", sans-serif; font-weight: 700; font-size: 38px;
    color: var(--navy);
  }
  .contact-band {
    position: absolute; left: 0; top: 984px; width: 510px; height: 126px;
    background: var(--grey-band); color: var(--white);
  }
  .contact-item { position: absolute; display: flex; align-items: center; gap: 5px; white-space: nowrap; }
  .contact-item svg { flex: none; }
  .phone { left: 30px; top: 5px; font-size: 25px; }
  .web { left: 255px; top: 9px; font-size: 19px; }
  .address {
    position: absolute; left: 0; width: 100%; top: 48px; text-align: center;
    font-size: 19px; line-height: 24px;
  }
</style>
</head>
<body>
  <article class="rack-card">
    <div class="hero-photo" role="img" aria-label="Photo of the golf course fairway lined with tall pine trees at sunrise"></div>
    <div class="club-seal"><span>Pinewood Bay<br>Golf Club</span></div>

    <h1 class="title">Summer Rates</h1>
    <p class="season">May 1 – September 30</p>

    <div class="rate-heading">18 Holes With Cart</div>
    <table class="rate-table primary">
      <tr><td class="slot is-light">7AM – 11AM</td><td class="price is-dark">$24</td></tr>
      <tr><td class="slot is-dark">11AM – 3PM</td><td class="price is-light">$19</td></tr>
      <tr><td class="slot is-light">3PM – Close</td><td class="price is-dark">$15</td></tr>
    </table>

    <table class="rate-table secondary">
      <tr><td class="slot is-light">9 Holes With Cart</td><td class="price is-dark">$15</td></tr>
      <tr><td class="slot is-dark">Walking</td><td class="price is-light">$12</td></tr>
    </table>

    <div class="kids-offer">
      <span>Children 15 and Under</span>
      <span><strong>FREE</strong> with Paid Adult</span>
    </div>

    <p class="lunch">Lunch Available Daily</p>
    <p class="lunch-hours">10AM – 3PM</p>

    <footer class="contact-band">
      <div class="contact-item phone">
        <svg width="20" height="20" viewBox="0 0 20 20" aria-hidden="true">
          <circle cx="10" cy="10" r="8.5" fill="none" stroke="#1e3d6b" stroke-width="1.6"/>
          <path d="M6.5 5.8c.6-.5 1.3-.4 1.6.2l.8 1.5c.2.5 0 1-.4 1.2l-.5.3c.5 1.2 1.3 2 2.5 2.6l.3-.5c.3-.4.8-.5 1.2-.3l1.5.8c.6.3.6 1 .2 1.6-.9 1-2.3 1-3.6.2-1.8-1-3.1-2.4-4-4.1-.6-1.3-.5-2.6.4-3.5z" fill="#1e3d6b"/>
        </svg>
        <span>555-014-2290</span>
      </div>
      <div class="contact-item web">
        <svg width="20" height="20" viewBox="0 0 20 20" aria-hidden="true" fill="none" stroke="#1e3d6b" stroke-width="1.5">
          <circle cx="10" cy="10" r="8.5"/>
          <ellipse cx="10" cy="10" rx="3.8" ry="8.5"/>
          <path d="M1.5 10h17M3 5.5h14M3 14.5h14"/>
        </svg>
        <span>www.pinewoodbaygc.com</span>
      </div>
      <div class="address">
        <div class="contact-item" style="position:static;justify-content:center;">
          <svg width="13" height="18" viewBox="0 0 13 18" aria-hidden="true">
            <path d="M6.5 0C2.9 0 0 2.8 0 6.3 0 11 6.5 18 6.5 18S13 11 13 6.3C13 2.8 10.1 0 6.5 0z" fill="#1e3d6b"/>
            <circle cx="6.5" cy="6.3" r="2.4" fill="#7c7c7c"/>
          </svg>
          <span>The Pinewood Bay Golf Club</span>
        </div>
        <div>4410 Heron Marsh Rd, Fairhaven, FL 30000</div>
      </div>
    </footer>
  </article>
</body>
</html>
```